Quillbrookes websites redesign

Www.quill-brookes.com needs to be redesigned along with updations. The incremental material will be provided for the updations. We are looking for complete redesign of the pages with the new content. The complete write up will be provided soon

Target Market(s)

Global

Coding

Coded - Design and coding required

Number of Pages Required

5+ page

Requirements
Must have
• A clean and slick design for the Consulting.
Should not have
• Too many pictures which reduces the speed of the site

```html
<!DOCTYPE html>
<html lang="en">
<head>
<meta charset="utf-8">
<title>Quillbrookes Consultancy</title>
<link href="https://fonts.googleapis.com/css2?family=Raleway:wght@400;500;600&family=Ubuntu:wght@400;500&display=swap" rel="stylesheet">
<style>
:root{
  --teal:#3aa3cc;
  --teal-dark:#2b87ad;
  --maroon:#7d2b2f;
  --ink:#2b2b2b;
  --body:#444;
  --footer:#3d3d3d;
  --caption:#3c3c3c;
  --white:#fff;
}
*{margin:0;padding:0;box-sizing:border-box}
html,body{width:1200px;height:2242px;overflow:hidden;background:var(--white)}
body{position:relative;font-family:"Raleway",sans-serif;color:var(--body)}
.abs{position:absolute}
.top-bar{left:0;top:0;width:1200px;height:7px;background:var(--teal)}
.header{left:0;top:7px;width:1200px;height:98px;background:var(--white)}
.brand{display:flex;align-items:center;gap:12px;font-family:"Ubuntu",sans-serif;font-weight:400}
.brand-mark{width:40px;height:40px;border-radius:50%;background:var(--maroon)}
.header .brand{left:99px;top:40px;font-size:34px;color:var(--maroon)}
.nav{top:55px;display:flex;font-size:16px;color:var(--ink)}
.nav a{position:absolute;white-space:nowrap;text-decoration:none;color:inherit}
.nav .active::after{content:"";position:absolute;left:-2px;right:-2px;top:30px;height:2px;background:var(--maroon)}
.hero{left:0;top:105px;width:1200px;height:554px;background:linear-gradient(90deg,#2a2c31 0%,#34373e 40%,#2c3f63 75%,#1d2c4f 100%)}
.hero-art{left:560px;top:105px;width:640px;height:554px;background:radial-gradient(circle at 55% 45%,#5ea6e8 0%,#2f64a8 25%,#253a66 55%,rgba(40,44,52,0) 80%)}
.hero .brand{left:99px;top:115px;font-size:30px;color:var(--white)}
.hero .brand-mark{background:var(--white);width:44px;height:44px}
.hero h1{left:99px;top:198px;width:460px;font-size:32px;line-height:42px;font-weight:600;color:var(--white)}
.hero p{left:99px;top:303px;width:400px;font-size:15px;line-height:23px;color:#e8e8e8}
.btn{display:flex;align-items:center;justify-content:center;border:1px solid;border-radius:3px;font-size:13px}
.hero .btn{left:99px;top:370px;width:115px;height:38px;border-color:#ddd;color:var(--white);font-size:15px}
.dots{left:99px;top:437px;display:flex;gap:20px}
.dots span{width:7px;height:7px;border-radius:50%;background:var(--white)}
.dots span.off{background:none;border:1px solid var(--white)}
.hero-shadow{left:60px;top:659px;width:1080px;height:24px;background:radial-gradient(ellipse at 50% 0%,rgba(0,0,0,.18),rgba(0,0,0,0) 70%)}
.section-title{left:0;width:1200px;display:flex;justify-content:center;align-items:center;gap:12px;font-family:"Ubuntu",sans-serif;font-weight:500;font-size:29px}
.section-title .dot{width:28px;height:28px;border-radius:50%}
.rule{left:565px;width:72px;height:2px}
.about-title{top:697px;color:var(--ink)}
.about-title .dot{background:var(--teal)}
.about-title em{font-style:normal;color:var(--maroon)}
.about-rule{top:750px;background:#999}
.lead{left:150px;top:782px;width:900px;text-align:center;font-size:15px;line-height:29px;color:var(--ink);letter-spacing:.3px}
.intro{left:99px;top:856px;width:1002px;text-align:center;font-size:13px;line-height:22px}
.connector{left:235px;top:1026px;width:730px;height:3px;background:#c9a3a3}
.node{width:20px;height:20px;border-radius:50%;border:2px solid var(--maroon);background:var(--white);top:1017px}
.node::after{content:"";position:absolute;left:5px;top:4px;border-left:6px solid var(--maroon);border-top:4px solid transparent;border-bottom:4px solid transparent}
.feature-icon{width:128px;height:128px;border-radius:50%;top:963px;display:flex;align-items:center;justify-content:center;box-shadow:4px 5px 0 rgba(0,0,0,.18)}
.feature{top:1108px;width:300px;text-align:center}
.feature h3{font-size:18px;font-weight:500;color:var(--ink);margin-bottom:12px}
.feature p{font-size:13px;line-height:22px;color:var(--body);width:270px;margin:0 auto}
.feature .btn{position:static;width:97px;height:32px;margin:14px auto 0;border-color:#555;color:var(--ink);border-radius:4px}
.founder{left:0;top:1297px;width:1200px;height:435px;background:var(--teal)}
.founder-title{top:1328px;color:var(--white)}
.founder-title .dot{background:var(--white)}
.founder-rule{top:1376px;background:rgba(255,255,255,.8)}
.photo{left:99px;top:1411px;width:429px;height:239px;background:linear-gradient(160deg,#3a3e78 0%,#56407a 45%,#9a4a50 75%,#b8722f 100%)}
.caption{left:99px;top:1650px;width:429px;height:51px;background:var(--caption);color:var(--white);display:flex;align-items:center;justify-content:center;font-family:"Ubuntu",sans-serif;font-weight:500;font-size:20px}
.bio{left:551px;top:1416px;width:550px;font-size:13px;line-height:21.7px;color:var(--white)}
.bio p+p{margin-top:10px}
.founder .btn{left:551px;top:362px;width:108px;height:36px;border-color:var(--white);color:var(--white)}
.partners{left:0;top:1732px;width:1200px;height:190px}
.partner{top:1812px;font-family:"Raleway",sans-serif;color:#333;text-align:center;white-space:nowrap}
.badge{left:535px;top:1773px;width:112px;height:112px;border-radius:50%;background:#3e3e3e;border:4px solid #ccc}
.footer{left:0;top:1922px;width:1200px;height:267px;background:var(--footer);color:#eee}
.footer .brand{left:99px;top:52px;font-size:26px;color:var(--white)}
.footer .brand-mark{width:34px;height:34px;background:var(--white)}
.footer-about{left:99px;top:105px;width:205px;font-size:12.5px;line-height:21px}
.col-head{top:56px;font-size:15px;letter-spacing:.3px}
.contact-list{left:347px;top:95px;font-size:13.5px;line-height:30px}
.contact-list li{list-style:none;display:flex;gap:14px;align-items:flex-start}
.contact-list svg{margin-top:9px;flex:none}
.links{left:667px;top:92px;font-size:13.5px;line-height:24px;list-style:none}
.field{left:849px;width:251px;height:34px;border:1px solid #aaa;font-size:13px;padding:9px 8px;color:#eee}
.submit{left:849px;top:191px;width:251px;height:35px;background:var(--teal);color:var(--white);font-size:13px;display:flex;align-items:center;justify-content:center}
.bottom{left:0;top:2189px;width:1200px;height:53px;background:linear-gradient(180deg,var(--teal),var(--teal-dark));color:var(--white);font-size:14px}
.bottom .copy{left:99px;top:17px}
.social{top:15px;width:24px;height:24px;border-radius:50%;border:1.5px solid var(--white)}
</style>
</head>
<body>
<div class="abs top-bar"></div>

<header class="abs header">
  <div class="abs brand"><span class="brand-mark"></span>Quillbrookes</div>
  <nav class="nav">
    <a class="active" style="left:468px;top:48px">Home</a>
    <a style="left:556px;top:48px">Founder</a>
    <a style="left:663px;top:48px">Consultancy</a>
    <a style="left:801px;top:48px">System</a>
    <a style="left:901px;top:48px">Case Studies</a>
    <a style="left:1042px;top:48px">Contact</a>
  </nav>
</header>

<section class="abs hero">
  <div class="abs brand"><span class="brand-mark"></span>Quillbrookes</div>
  <h1 class="abs">World Merchandising Trade 2012 ( USD Billion)</h1>
  <p class="abs">We invest actively in developing technology platform for better distribution, disintermediation</p>
  <a class="abs btn">Read More</a>
  <div class="abs dots"><span></span><span class="off"></span><span></span></div>
</section>
<div class="abs hero-art" role="img" aria-label="Businessman holding a glowing globe linked to people icons, with a laptop, tablet and phone"></div>
<div class="abs hero-shadow"></div>

<h2 class="abs section-title about-title"><span class="dot"></span>About <em>Quillbrookes</em></h2>
<div class="abs rule about-rule"></div>
<p class="abs lead">QUILLBROOKES CONSULTANCY LIMITED CAPITALIZES ON SYNERGIES ARISING FROM TRADE AND INVESTMENT LINKAGES BETWEEN COUNTRIES AND KNOWLEDGE OF TRADITIONAL</p>
<p class="abs intro">The Consultancy provides bank neutral views to Corporates and SMEs in Asian emerging markets and helps in improving financial structure and efficient use of funds. Our endeavor is to provide a distinct bottom line advantage to our clients. The primary focus is in regionalisation of the banking relationship across the globe, providing structured finance solutions and off balance sheet solutions.</p>

<div class="abs connector"></div>
<div class="abs node" style="left:411px"></div>
<div class="abs node" style="left:770px"></div>

<div class="abs feature-icon" style="left:171px;background:var(--maroon)">
  <svg width="56" height="56" viewBox="0 0 56 56" fill="none" stroke="#fff" stroke-width="4"><circle cx="28" cy="28" r="22"/><circle cx="28" cy="28" r="10"/><path d="M13 13l8 8M43 13l-8 8M13 43l8-8M43 43l-8-8"/></svg>
</div>
<div class="abs feature-icon" style="left:536px;background:var(--teal)">
  <svg width="56" height="56" viewBox="0 0 56 56" fill="none" stroke="#fff" stroke-width="5" stroke-linecap="round"><path d="M24 18l6-6a8 8 0 0 1 12 12l-6 6"/><path d="M32 38l-6 6a8 8 0 0 1-12-12l6-6"/><path d="M22 34l12-12"/></svg>
</div>
<div class="abs feature-icon" style="left:901px;background:var(--teal)">
  <svg width="56" height="56" viewBox="0 0 56 56" fill="none" stroke="#fff" stroke-width="5" stroke-linecap="round"><rect x="10" y="10" width="36" height="36" rx="8" transform="rotate(45 28 28)"/><path d="M18 18l20 20"/></svg>
</div>

<div class="abs feature" style="left:85px">
  <h3>Mitigation Techniques</h3>
  <p>We invest actively in developing technology platform for better distribution, disintermediation, efficient</p>
  <a class="btn">Read More</a>
</div>
<div class="abs feature" style="left:450px">
  <h3>Export Credit Agency</h3>
  <p>We invest actively in developing technology platform for better distribution, disintermediation, efficient</p>
  <a class="btn">Read More</a>
</div>
<div class="abs feature" style="left:815px">
  <h3>Trade Origination Distribution</h3>
  <p>We invest actively in developing technology platform for better distribution, disintermediation, efficient</p>
  <a class="btn">Read More</a>
</div>

<section class="abs founder">
  <a class="abs btn">Read More</a>
</section>
<h2 class="abs section-title founder-title"><span class="dot"></span>About Founder</h2>
<div class="abs rule founder-rule"></div>
<div class="abs photo" role="img" aria-label="Founder speaking at a podium with flowers at an international trade conference"></div>
<div class="abs caption">Meera Castell</div>
<div class="abs bio">
  <p>Ms. Meera Castell is the founder director of Quillbrookes Consultancy Limited (QCL) based at Hong Kong. Meera worked as the Alternate Chief Executive of Northgate Bank, Hong Kong Branch until Jan 2013, heading Corporate Banking business in North Asia and Export Credit Agency business globally. During her tenure, both the businesses increased multifold.</p>
  <p>Meera started her banking career with Northgate Bank Ltd, India's second largest bank in the year 2002 and in the next 10 years handled multiple leadership responsibilities in the Corporate, Institutional and International Banking space across India, North Asia, Americas and Europe. Meera's Corporate Banking experience includes her roles as Zonal Manager for Western Region in India.</p>
</div>

<section class="abs partners" aria-label="Partners"></section>
<div class="abs partner" style="left:138px;top:1820px;font-size:13px;font-weight:600;letter-spacing:3px">MARLOW PIKE</div>
<div class="abs partner" style="left:334px;top:1814px;font-size:22px">conveyance</div>
<div class="abs badge"></div>
<div class="abs partner" style="left:725px;top:1822px;font-size:11px;font-weight:600;letter-spacing:2px">SOLACE HEALTH</div>
<div class="abs partner" style="left:915px;top:1808px;font-size:30px">Venture</div>

<footer class="abs footer">
  <div class="abs brand"><span class="brand-mark"></span>Quillbrookes</div>
  <p class="abs footer-about">The consultancy for the Banks and Non Banking Financial Institutions is focused on risk mitigation techniques, Export Credit Agency business</p>
  <h4 class="abs col-head" style="left:347px;font-weight:500">CONTACT US</h4>
  <ul class="abs contact-list">
    <li><svg width="12" height="14" viewBox="0 0 12 14"><path d="M6 0a5 5 0 0 1 5 5c0 4-5 9-5 9S1 9 1 5a5 5 0 0 1 5-5z" fill="#fff"/><circle cx="6" cy="5" r="2" fill="#3d3d3d"/></svg><span>Quillbrookes Consultancy Ltd<br>Unit 05, 8th Floor, Hong Kong</span></li>
    <li><svg width="12" height="10" viewBox="0 0 12 10"><rect width="12" height="10" rx="1" fill="#fff"/><path d="M0 1l6 5 6-5" stroke="#3d3d3d" fill="none"/></svg><span>Email: query@quill-brookes.com</span></li>
    <li><svg width="12" height="12" viewBox="0 0 12 12"><rect width="12" height="12" rx="2" fill="#fff"/><path d="M3 3c0 4 2 6 6 6l1-2-2-1-1 1c-1-.5-2-1.5-2.5-2.5l1-1-1-2z" fill="#3d3d3d"/></svg><span>Phone: +852-21004567</span></li>
  </ul>
  <h4 class="abs col-head" style="left:667px;font-weight:500">QUICK LINKS</h4>
  <ul class="abs links"><li>Home</li><li>Founder</li><li>Consultancy</li><li>System</li><li>Contact</li></ul>
  <h4 class="abs col-head" style="left:846px;font-weight:500">QUERY FORM</h4>
  <div class="abs field" style="top:97px">Name</div>
  <div class="abs field" style="top:145px">Email</div>
  <div class="abs submit">SIGN UP NOW</div>
</footer>

<div class="abs bottom">
  <span class="abs copy">© 2016 &nbsp;Quillbrookes . All Rights Reserved</span>
  <span class="abs social" style="left:947px"></span>
  <span class="abs social" style="left:989px"></span>
  <span class="abs social" style="left:1033px"></span>
  <span class="abs social" style="left:1076px"></span>
</div>
</body>
</html>
```